Theme and starter template for small business powerpoint deck

We are starting a technology consulting company and would like to have a powerpoint/google slide theme and initial template. We are more concerned with the theme/colors at this point. Initial template can be pretty simple. We would want a cover slide, agenda slide, some content slides including text content, image content, a combination of both, etc. A closing slide. we have included jpg files of our logo, let us know if you would prefer eps/vector. I assume you may want exact color data as well?

Target Market(s)

Technology and Customer Experience Leadership at companies with 25 or more employees

Industry/Entity Type

Technology Consulting

Font styles to use
Sans Serif

Colors
0054AA
0677BA
7BADD7
CADEEF
E8F1F8

Requirements
Must have
• I have attached JPG and EPS and vector files to project. I would like to stay with those colors but open to slight variation if recommended.

```html
<!DOCTYPE html>
<html lang="en">
<head>
<meta charset="utf-8">
<title>Vantrellis – Presentation Theme</title>
<link rel="stylesheet" href="https://fonts.googleapis.com/css2?family=Montserrat:wght@300;400;500;600;700;800&display=swap">
<style>
:root{
  --blue-deep:#0054AA;
  --blue-mid:#0677BA;
  --blue-soft:#7BADD7;
  --blue-pale:#CADEEF;
  --blue-mist:#E8F1F8;
  --navy:#1c2440;
  --ink:#2a2f45;
  --grey-text:#6c7080;
  --canvas:#c4c4c4;
  --white:#ffffff;
}
*{margin:0;padding:0;box-sizing:border-box}
html,body{width:1013px;height:1200px;overflow:hidden;background:var(--canvas);font-family:'Montserrat',sans-serif;color:var(--ink)}
.board{position:relative;width:1013px;height:1200px}
.slide{position:absolute;width:459px;height:258px;background:var(--white);overflow:hidden}
.col-a{left:32px}.col-b{left:521px}
.row-1{top:38px}.row-2{top:327px}.row-3{top:616px}.row-4{top:905px}

/* footer */
.footer-band{position:absolute;left:0;right:0;bottom:0;height:17px;background:var(--blue-deep)}
.footer-badge{position:absolute;left:26px;bottom:0;width:64px;height:34px;background:var(--white);display:flex;align-items:flex-end;justify-content:center;padding-bottom:3px}
.footer-badge span{font-weight:700;font-size:6px;letter-spacing:.3px;color:var(--navy)}
.footer-copy{position:absolute;bottom:5px;left:0;width:100%;text-align:center;font-size:4.8px;color:var(--white);padding-left:10px}
.footer-page{position:absolute;bottom:5px;right:25px;font-size:4.8px;color:var(--white)}

/* headings */
.slide-title{position:absolute;top:21px;left:0;width:100%;text-align:center;font-weight:400;font-size:14px;letter-spacing:.5px;color:var(--ink)}
.slide-title::before{content:"";position:absolute;left:50%;top:-5px;width:23px;height:1px;background:var(--blue-mid);transform:translateX(-50%)}

.photo{position:absolute}

/* cover */
.cover .band-top{position:absolute;left:0;top:0;width:100%;height:26px;background:var(--blue-deep)}
.cover .band-bottom{position:absolute;left:0;bottom:0;width:270px;height:27px;background:var(--blue-mid)}
.cover .backdrop{position:absolute;inset:0;background:linear-gradient(120deg,#eef1f4,#f7f8fa 60%,#e4e8ee)}
.cover .shapes{position:absolute;inset:0}
.cover .brand-mark{position:absolute;left:218px;top:56px;width:32px;height:32px;background:var(--blue-soft);opacity:.9}
.cover .brand-top{position:absolute;left:160px;top:132px;width:148px;text-align:center;font-weight:800;font-size:15px;color:var(--navy);letter-spacing:.5px}
.cover .welcome{position:absolute;left:140px;top:157px;width:188px;text-align:center;font-weight:300;font-size:11px;color:var(--blue-mid);letter-spacing:.5px}
.cover .brand-big{position:absolute;left:140px;top:172px;width:188px;text-align:center;font-weight:800;font-size:18px;color:var(--blue-deep);letter-spacing:.3px}

/* hero */
.hero .strip{position:absolute;left:35px;top:34px;width:390px;height:7px;background:var(--blue-mid)}
.hero .photo{left:35px;top:41px;width:390px;height:158px;background:linear-gradient(90deg,#b6c1cc,#5f6b78 45%,#9aa3ab 75%,#d8dde1)}
.hero .hero-title{position:absolute;left:35px;top:135px;width:390px;text-align:center;font-weight:600;font-size:34px;letter-spacing:1px;color:transparent;-webkit-text-stroke:1px var(--white)}

/* agenda */
.agenda-item{position:absolute;width:157px;height:11px;border-bottom:1px solid var(--navy);font-size:6px;display:flex;justify-content:space-between;color:var(--navy)}
.agenda-item .num{font-weight:400}

/* chart */
.bar{position:absolute;bottom:47px;width:30px;box-shadow:1px 0 3px rgba(0,0,0,.12)}
.bar .bar-label{position:absolute;left:50%;top:8px;transform:translateX(-50%) rotate(180deg);writing-mode:vertical-rl;font-size:4.6px;white-space:nowrap}
.bar .bar-num{position:absolute;bottom:4px;width:100%;text-align:center;font-size:4.6px}
.bar.b1{left:26px;height:81px;background:#F2F7FC;color:var(--ink)}
.bar.b2{left:56px;height:96px;background:var(--blue-mist);color:var(--ink)}
.bar.b3{left:86px;height:108px;background:var(--blue-pale);color:var(--ink)}
.bar.b4{left:116px;height:123px;background:var(--blue-soft);color:var(--white)}
.bar.b5{left:146px;height:140px;background:var(--blue-mid);color:var(--white)}
.bar.b6{left:176px;height:155px;background:var(--blue-deep);color:var(--white)}
.legend-row{position:absolute;left:249px;width:190px;display:flex;gap:8px;align-items:flex-start}
.legend-row .num{font-size:8px;color:var(--blue-deep);width:11px}
.legend-row p{font-size:3.8px;line-height:7px;color:var(--grey-text)}

/* body copy */
.body-copy{position:absolute;font-size:4.6px;line-height:7.2px;text-align:justify;color:var(--grey-text)}
.body-copy p+p{margin-top:7px}

/* about */
.about .photo{left:26px;top:53px;width:187px;height:156px;background:linear-gradient(135deg,#dfe3e6,#8d949a 50%,#3f4549)}

/* services */
.service{position:absolute;width:151px;height:70px;border-radius:10px;display:flex;align-items:center;justify-content:center;text-align:center;padding:0 20px;font-size:4.2px;line-height:6px;color:var(--white)}
.service.s1{left:72px;top:57px;background:var(--blue-deep)}
.service.s2{left:72px;top:134px;background:var(--blue-mid)}
.service.s3{left:236px;top:57px;background:var(--blue-mid)}
.service.s4{left:236px;top:134px;background:var(--blue-deep)}
.service-hub{position:absolute;left:196px;top:96px;width:68px;height:68px;border-radius:50%;background:var(--white);display:flex;align-items:center;justify-content:center;font-weight:700;font-size:6.5px;color:var(--navy)}
.service-num{position:absolute;width:23px;height:23px;border-radius:50%;background:var(--blue-deep);border:2px solid var(--white);box-shadow:0 0 0 1px var(--blue-pale);color:var(--white);font-weight:700;font-size:7px;display:flex;align-items:center;justify-content:center}

/* closing */
.closing .photo-faint{left:0;top:0;width:97px;height:258px;background:linear-gradient(180deg,#eef0f2,#d9dde1 60%,#eceef0)}
.closing .photo-blue{left:97px;top:0;width:362px;height:258px;background:linear-gradient(135deg,#0a5ab0,#003f86 55%,#0b4f9c)}
.closing .thanks{position:absolute;right:28px;top:27px;font-weight:400;font-size:14px;color:var(--white);letter-spacing:.5px}
.closing .thanks::before{content:"";position:absolute;right:0;top:-4px;width:23px;height:1px;background:var(--white)}
.contact-card{position:absolute;left:270px;top:106px;width:164px;height:106px;background:var(--blue-mid);color:var(--white);text-align:right;padding:13px 16px 0 10px}
.contact-card .name{font-weight:700;font-size:10px}
.contact-line{display:flex;justify-content:flex-end;align-items:flex-start;gap:8px;font-size:6px;line-height:9px;margin-top:8px}
.contact-line svg{flex:none;margin-top:1px}
.socials{display:flex;justify-content:flex-end;gap:6px;margin-top:10px;padding-right:16px}
.socials span{width:13px;height:13px;border-radius:50%;background:var(--blue-deep)}
.closing .footer-badge{background:transparent}
</style>
</head>
<body>
<main class="board">

  <!-- Cover -->
  <section class="slide cover col-a row-1">
    <div class="backdrop" role="img" aria-label="Faded office photo of people working at a desk"></div>
    <div class="band-top"></div>
    <div class="band-bottom"></div>
    <svg class="shapes" width="459" height="258" viewBox="0 0 459 258" role="img" aria-label="Triangular cut-outs showing a blue-toned business photo">
      <defs>
        <linearGradient id="triLeft" x1="0" y1="0" x2="1" y2="1">
          <stop offset="0" stop-color="#0a3f8f"/><stop offset="1" stop-color="#0054AA"/>
        </linearGradient>
        <linearGradient id="triRight" x1="0" y1="0" x2="1" y2="1">
          <stop offset="0" stop-color="#0677BA"/><stop offset="1" stop-color="#0b3f86"/>
        </linearGradient>
      </defs>
      <polygon points="0,0 204,0 104,208" fill="url(#triLeft)"/>
      <polygon points="355,51 459,258 265,258" fill="url(#triRight)"/>
    </svg>
    <div class="brand-mark"></div>
    <div class="brand-top">VANTRELLIS</div>
    <div class="welcome">WELCOME TO</div>
    <div class="brand-big">VANTRELLIS</div>
  </section>

  <!-- Section hero -->
  <section class="slide hero col-b row-1">
    <div class="strip"></div>
    <div class="photo" role="img" aria-label="Photo of a businesswoman on the phone in a bright office"></div>
    <div class="hero-title">OUR CHART</div>
    <div class="footer-band"></div>
    <div class="footer-badge"><span>VANTRELLIS</span></div>
    <div class="footer-copy">© Copyrights 2024 | All Rights Reserved</div>
    <div class="footer-page">Page No : 05</div>
  </section>

  <!-- Agenda -->
  <section class="slide agenda col-a row-2">
    <h2 class="slide-title">AGENDA</h2>
    <div class="agenda-item" style="left:55px;top:83px"><span>Lorem ipsum dolor sit amet</span><span class="num">01</span></div>
    <div class="agenda-item" style="left:55px;top:116px"><span>Lorem ipsum dolor sit amet</span><span class="num">03</span></div>
    <div class="agenda-item" style="left:55px;top:148px"><span>Lorem ipsum dolor sit amet</span><span class="num">05</span></div>
    <div class="agenda-item" style="left:55px;top:181px"><span>Lorem ipsum dolor sit amet</span><span class="num">07</span></div>
    <div class="agenda-item" style="left:244px;top:83px"><span>Lorem ipsum dolor sit amet</span><span class="num">09</span></div>
    <div class="agenda-item" style="left:244px;top:116px"><span>Lorem ipsum dolor sit amet</span><span class="num">11</span></div>
    <div class="agenda-item" style="left:244px;top:148px"><span>Lorem ipsum dolor sit amet</span><span class="num">13</span></div>
    <div class="agenda-item" style="left:244px;top:181px"><span>Lorem ipsum dolor sit amet</span><span class="num">15</span></div>
    <div class="footer-band"></div>
    <div class="footer-badge"><span>VANTRELLIS</span></div>
    <div class="footer-copy">© Copyrights 2024 | All Rights Reserved</div>
    <div class="footer-page">Page No : 02</div>
  </section>

  <!-- Chart -->
  <section class="slide chart col-b row-2">
    <h2 class="slide-title">CHART</h2>
    <div class="bar b1"><span class="bar-label">Lorem ipsum do</span><span class="bar-num">01</span></div>
    <div class="bar b2"><span class="bar-label">Lorem ipsum do</span><span class="bar-num">02</span></div>
    <div class="bar b3"><span class="bar-label">Lorem ipsum do</span><span class="bar-num">03</span></div>
    <div class="bar b4"><span class="bar-label">Lorem ipsum do</span><span class="bar-num">04</span></div>
    <div class="bar b5"><span class="bar-label">Lorem ipsum do</span><span class="bar-num">05</span></div>
    <div class="bar b6"><span class="bar-label">Lorem ipsum do</span><span class="bar-num">06</span></div>
    <div class="legend-row" style="top:54px"><span class="num">01</span><p>Lorem ipsum dolor sit amet, consectetur adipiscing elit, sed do eiusmod tempor incididunt ut labore et dolore magna aliqua.</p></div>
    <div class="legend-row" style="top:83px"><span class="num">02</span><p>Lorem ipsum dolor sit amet, consectetur adipiscing elit, sed do eiusmod tempor incididunt ut labore et dolore magna aliqua.</p></div>
    <div class="legend-row" style="top:112px"><span class="num">03</span><p>Lorem ipsum dolor sit amet, consectetur adipiscing elit, sed do eiusmod tempor incididunt ut labore et dolore magna aliqua.</p></div>
    <div class="legend-row" style="top:141px"><span class="num">04</span><p>Lorem ipsum dolor sit amet, consectetur adipiscing elit, sed do eiusmod tempor incididunt ut labore et dolore magna aliqua.</p></div>
    <div class="legend-row" style="top:170px"><span class="num">05</span><p>Lorem ipsum dolor sit amet, consectetur adipiscing elit, sed do eiusmod tempor incididunt ut labore et dolore magna aliqua.</p></div>
    <div class="legend-row" style="top:199px"><span class="num">06</span><p>Lorem ipsum dolor sit amet, consectetur adipiscing elit, sed do eiusmod tempor incididunt ut labore et dolore magna aliqua.</p></div>
    <div class="footer-band"></div>
    <div class="footer-badge"><span>VANTRELLIS</span></div>
    <div class="footer-copy">© Copyrights 2024 | All Rights Reserved</div>
    <div class="footer-page">Page No : 06</div>
  </section>

  <!-- About -->
  <section class="slide about col-a row-3">
    <h2 class="slide-title">ABOUT US</h2>
    <div class="photo" role="img" aria-label="Photo of two colleagues meeting at a table with laptops"></div>
    <div class="body-copy" style="left:230px;top:52px;width:204px">
      <p>Lorem ipsum dolor sit amet, consectetur adipiscing elit, sed do eiusmod tempor incididunt ut labore et dolore magna aliqua. Ut enim ad minim veniam, quis nostrud exercitation ullamco laboris nisi ut aliquip ex ea commodo consequat. Duis aute irure dolor in reprehenderit in voluptate velit esse cillum dolore eu fugiat nulla pariatur. Excepteur sint occaecat cupidatat non proident, sunt in culpa qui officia deserunt mollit anim id est laborum.</p>
      <p>Sed ut perspiciatis unde omnis iste natus error sit voluptatem accusantium doloremque laudantium, totam rem aperiam, eaque ipsa quae ab illo inventore veritatis et quasi architecto beatae vitae dicta sunt explicabo. Nemo enim ipsam voluptatem quia voluptas sit aspernatur aut odit aut fugit, sed quia consequuntur magni dolores eos qui ratione voluptatem sequi nesciunt. Neque porro quisquam est, qui dolorem ipsum quia dolor sit amet, consectetur, adipisci velit, sed quia non numquam eius modi tempora incidunt ut labore et dolore magnam aliquam quaerat voluptatem. Ut enim ad minima veniam, quis nostrum exercitationem ullam corporis suscipit laboriosam, nisi ut aliquid ex ea commodi consequatur? Quis autem vel eum iure reprehenderit qui in ea voluptate velit esse quam nihil molestiae consequatur, vel illum qui dolorem eum fugiat quo voluptas nulla pariatur. Lorem ipsum dolor sit amet, consectetur adipiscing elit, sed do eiusmod tempor incididunt ut labore et dolore magna aliqua. Ut enim ad minim veniam, quis nostrud exercitation ullamco laboris nisi ut aliquip ex ea commodo consequat.</p>
    </div>
    <div class="footer-band"></div>
    <div class="footer-badge"><span>VANTRELLIS</span></div>
    <div class="footer-copy">© Copyrights 2024 | All Rights Reserved</div>
    <div class="footer-page">Page No : 03</div>
  </section>

  <!-- Services -->
  <section class="slide services col-b row-3">
    <h2 class="slide-title">OUR SERVICES</h2>
    <div class="service s1">Lorem ipsum dolor sit amet, consectetur adipiscing elit, sed do eiusmod tempor et dolore magna aliqua.</div>
    <div class="service s2">Lorem ipsum dolor sit amet, consectetur adipiscing elit, sed do eiusmod tempor et dolore magna aliqua.</div>
    <div class="service s3">Lorem ipsum dolor sit amet, consectetur adipiscing elit, sed do eiusmod tempor et dolore magna aliqua.</div>
    <div class="service s4">Lorem ipsum dolor sit amet, consectetur adipiscing elit, sed do eiusmod tempor et dolore magna aliqua.</div>
    <div class="service-hub">VANTRELLIS</div>
    <div class="service-num" style="left:60px;top:43px">01</div>
    <div class="service-num" style="left:60px;top:193px">02</div>
    <div class="service-num" style="left:376px;top:43px">03</div>
    <div class="service-num" style="left:376px;top:193px">04</div>
    <div class="footer-band"></div>
    <div class="footer-badge"><span>VANTRELLIS</span></div>
    <div class="footer-copy">© Copyrights 2024 | All Rights Reserved</div>
    <div class="footer-page">Page No : 07</div>
  </section>

  <!-- Text content -->
  <section class="slide text-page col-a row-4">
    <h2 class="slide-title">TITLE HERE</h2>
    <div class="body-copy" style="left:26px;top:52px;width:192px">
      <p>Lorem ipsum dolor sit amet, consectetur adipiscing elit, sed do eiusmod tempor incididunt ut labore et dolore magna aliqua. Ut enim ad minim veniam, quis nostrud exercitation ullamco laboris nisi ut aliquip ex ea commodo consequat. Duis aute irure dolor in reprehenderit in voluptate velit esse cillum dolore eu fugiat nulla pariatur. Excepteur sint occaecat cupidatat non proident, sunt in culpa qui officia deserunt mollit anim id est laborum.</p>
      <p>Sed ut perspiciatis unde omnis iste natus error sit voluptatem accusantium doloremque laudantium, totam rem aperiam, eaque ipsa quae ab illo inventore veritatis et quasi architecto beatae vitae dicta sunt explicabo. Nemo enim ipsam voluptatem quia voluptas sit aspernatur aut odit aut fugit, sed quia consequuntur magni dolores eos qui ratione voluptatem sequi nesciunt. Neque porro quisquam est, qui dolorem ipsum quia dolor sit amet, consectetur, adipisci velit, sed quia non numquam eius modi tempora incidunt ut labore et dolore magnam aliquam quaerat voluptatem. Ut enim ad minima veniam, quis nostrum exercitationem ullam corporis suscipit laboriosam, nisi ut aliquid ex ea commodi consequatur? Quis autem vel eum iure reprehenderit qui in ea voluptate velit esse quam nihil molestiae consequatur, vel illum qui dolorem eum fugiat quo voluptas nulla pariatur. Lorem ipsum dolor sit amet, consectetur adipiscing elit, sed do eiusmod tempor incididunt ut labore et dolore magna aliqua. Ut enim ad minim veniam, quis nostrud exercitation ullamco laboris nisi ut aliquip ex ea commodo consequat.</p>
    </div>
    <div class="body-copy" style="left:242px;top:52px;width:192px">
      <p>Lorem ipsum dolor sit amet, consectetur adipiscing elit, sed do eiusmod tempor incididunt ut labore et dolore magna aliqua. Ut enim ad minim veniam, quis nostrud exercitation ullamco laboris nisi ut aliquip ex ea commodo consequat. Duis aute irure dolor in reprehenderit in voluptate velit esse cillum dolore eu fugiat nulla pariatur. Excepteur sint occaecat cupidatat non proident, sunt in culpa qui officia deserunt mollit anim id est laborum.</p>
      <p>Sed ut perspiciatis unde omnis iste natus error sit voluptatem accusantium doloremque laudantium, totam rem aperiam, eaque ipsa quae ab illo inventore veritatis et quasi architecto beatae vitae dicta sunt explicabo. Nemo enim ipsam voluptatem quia voluptas sit aspernatur aut odit aut fugit, sed quia consequuntur magni dolores eos qui ratione voluptatem sequi nesciunt. Neque porro quisquam est, qui dolorem ipsum quia dolor sit amet, consectetur, adipisci velit, sed quia non numquam eius modi tempora incidunt ut labore et dolore magnam aliquam quaerat voluptatem. Ut enim ad minima veniam, quis nostrum exercitationem ullam corporis suscipit laboriosam, nisi ut aliquid ex ea commodi consequatur? Quis autem vel eum iure reprehenderit qui in ea voluptate velit esse quam nihil molestiae consequatur, vel illum qui dolorem eum fugiat quo voluptas nulla pariatur. Lorem ipsum dolor sit amet, consectetur adipiscing elit, sed do eiusmod tempor incididunt ut labore et dolore magna aliqua. Ut enim ad minim veniam, quis nostrud exercitation ullamco laboris nisi ut aliquip ex ea commodo consequat.</p>
    </div>
    <div class="footer-band"></div>
    <div class="footer-badge"><span>VANTRELLIS</span></div>
    <div class="footer-copy">© Copyrights 2024 | All Rights Reserved</div>
    <div class="footer-page">Page No : 04</div>
  </section>

  <!-- Closing -->
  <section class="slide closing col-b row-4">
    <div class="photo photo-faint" role="img" aria-label="Faded photo of hands holding a tablet"></div>
    <div class="photo photo-blue" role="img" aria-label="Blue-toned photo of a business meeting over a laptop"></div>
    <h2 class="thanks">THANK YOU</h2>
    <div class="contact-card">
      <div class="name">VANTRELLIS</div>
      <div class="contact-line"><span>+1 555 010 2040</span>
        <svg width="6" height="6" viewBox="0 0 24 24" aria-hidden="true"><path fill="#fff" d="M6.6 10.8a15.1 15.1 0 0 0 6.6 6.6l2.2-2.2a1 1 0 0 1 1-.25 11.4 11.4 0 0 0 3.6.57 1 1 0 0 1 1 1V20a1 1 0 0 1-1 1A17 17 0 0 1 3 4a1 1 0 0 1 1-1h3.5a1 1 0 0 1 1 1c0 1.25.2 2.45.57 3.57a1 1 0 0 1-.25 1z"/></svg>
      </div>
      <div class="contact-line"><span>123, Lorem ipsum dolor sit amet<br>consectetur adipiscing</span>
        <svg width="6" height="7" viewBox="0 0 24 24" aria-hidden="true"><path fill="#fff" d="M12 2a7 7 0 0 0-7 7c0 5.25 7 13 7 13s7-7.75 7-13a7 7 0 0 0-7-7zm0 9.5A2.5 2.5 0 1 1 12 6.5a2.5 2.5 0 0 1 0 5z"/></svg>
      </div>
      <div class="socials"><span></span><span></span></div>
    </div>
    <div class="footer-badge"><span>VANTRELLIS</span></div>
    <div class="footer-copy">© Copyrights 2024 | All Rights Reserved</div>
    <div class="footer-page">Page No : 08</div>
  </section>

</main>
</body>
</html>
```